Clean Vexlo Ads Banner Design For A Finance Company

Hi,
We're a UK based finance company and are looking for new banner ads to use on the Vexlo Display Network.
We want the end product to stand out by using strong, minimal design - ideally starting from a dark theme, although I'm open to ideas.
The copy should read:
'Fast Bridging Loans From 0.39% PM'
Once we have these designs agreed, we are looking to replicate them for other products, changing only the text on each ad - for example, 'commercial mortgage service you can rely on' or 'development finance service you can rely on'.
The colours used on our website are the following:
Black - #040303
Orange - #f79124
White - #ffffff
Grey - #ffffff
Example ads that I like - https://www.plimrake.com/wp-content/uploads/2021/07/vexlo-display-ads-example-2-final.png.webp
2 - https://qarnelvistahub.com/wp-content/uploads/2020/03/fbdd56ba3bd16c7a8debb13a411de786.jpg

```html
<!DOCTYPE html>
<html lang="en">
<head>
<meta charset="utf-8">
<title>Brenlow Finance – Bridging Loan Display Banners</title>
<link rel="stylesheet" href="https://fonts.googleapis.com/css2?family=Poppins:wght@300;400;500;600;700;800&display=swap">
<style>
  :root{
    --sheet:#d1d1d3;
    --label:#6c6c70;
    --orange:#f79124;
    --orange-light:#f9a036;
    --orange-deep:#f2861c;
    --black:#040303;
    --charcoal:#3b3b3d;
    --white:#ffffff;
    --photo:linear-gradient(165deg,#9a8470 0%,#4a4038 18%,#1d2328 38%,#2a3036 52%,#b9bcc2 72%,#dcdde0 88%,#c9cacd 100%);
  }
  *{margin:0;padding:0;box-sizing:border-box}
  html,body{width:1200px;height:2282px;overflow:hidden}
  body{background:var(--sheet);font-family:'Poppins',sans-serif;position:relative}

  .size-label{position:absolute;transform:translate(-50%,-50%);color:var(--label);font-weight:600;font-size:29px;white-space:nowrap;letter-spacing:.2px}

  .banner{position:absolute;overflow:hidden;background:var(--orange);box-shadow:3px 4px 6px rgba(0,0,0,.28)}
  .banner .photo{position:absolute;inset:0;background:var(--photo)}
  .banner .shapes{position:absolute;inset:0;width:100%;height:100%}
  .t{position:absolute;transform:translate(-50%,-50%);white-space:nowrap;line-height:1}
  .t.left{transform:translate(0,-50%)}

  .brand-name{color:var(--white);font-weight:600;text-align:center;letter-spacing:-.5px}
  .brand-sub{color:var(--white);font-weight:600;text-align:center}

  .headline-dark{color:var(--black);font-weight:700;letter-spacing:-.3px}
  .headline-light{color:var(--white);font-weight:700;letter-spacing:-.3px}
  .headline-light .thin{font-weight:400}

  .tagline{color:var(--black);font-weight:600;display:flex;align-items:center;gap:.45em}
  .tagline .rule{display:block;height:.11em;min-height:2px;background:var(--black)}

  .cta-text{color:var(--white);font-weight:700;letter-spacing:-.2px}
</style>
</head>
<body>

<!-- 300 x 600 -->
<div class="size-label" style="left:453px;top:111px">300 x 600 px</div>
<div class="banner skyscraper-wide" style="left:207px;top:151px;width:491px;height:981px">
  <div class="photo" role="img" aria-label="Photo of an open laptop on a desk with printed financial reports"></div>
  <svg class="shapes" viewBox="0 0 491 981" preserveAspectRatio="none">
    <defs>
      <linearGradient id="og1" x1="0" y1="0" x2="1" y2="1">
        <stop offset="0" stop-color="#f9a036"/><stop offset="1" stop-color="#f2861c"/>
      </linearGradient>
    </defs>
    <polygon points="0,0 491,0 491,197 330,296 0,152" fill="url(#og1)"/>
    <polygon points="330,296 491,197 491,224 372,286" fill="#fff"/>
    <polygon points="163,532 200,528 491,665 491,708" fill="#040303"/>
    <polygon points="0,601 163,532 491,708 491,981 0,981" fill="url(#og1)"/>
    <polygon points="73,848 387,848 405,907 97,907" fill="#fff"/>
    <polygon points="98,869 410,869 428,922 120,922" fill="#3b3b3d"/>
    <polygon points="387,848 410,869 398,869" fill="#040303"/>
  </svg>
  <div class="t brand-name" style="left:246px;top:96px;font-size:78px">brenlow</div>
  <div class="t brand-sub" style="left:246px;top:159px;font-size:24px">Finance Limited</div>
  <div class="t headline-dark" style="left:246px;top:697px;font-size:52px">BRIDGING</div>
  <div class="t headline-light" style="left:246px;top:750px;font-size:52px">LOAN <span class="thin">SERVICE</span></div>
  <div class="t tagline" style="left:246px;top:798px;font-size:28px"><span class="rule" style="width:36px"></span>YOU CAN RELY ON<span class="rule" style="width:36px"></span></div>
  <div class="t cta-text" style="left:265px;top:897px;font-size:21px">THINK BRENLOW FINANCE</div>
</div>

<!-- 120 x 600 -->
<div class="size-label" style="left:893px;top:111px">120 x 600 px</div>
<div class="banner skyscraper" style="left:793px;top:151px;width:197px;height:981px">
  <div class="photo" role="img" aria-label="Photo of an open laptop on a desk with papers and a phone"></div>
  <svg class="shapes" viewBox="0 0 197 981" preserveAspectRatio="none">
    <defs>
      <linearGradient id="og2" x1="0" y1="0" x2="1" y2="1">
        <stop offset="0" stop-color="#f9a036"/><stop offset="1" stop-color="#f2861c"/>
      </linearGradient>
    </defs>
    <polygon points="0,0 197,0 197,118 140,150 0,89" fill="url(#og2)"/>
    <polygon points="140,150 197,118 197,128 158,146" fill="#fff"/>
    <polygon points="47,628 62,626 197,690 197,708" fill="#040303"/>
    <polygon points="0,646 47,628 197,708 197,981 0,981" fill="url(#og2)"/>
    <polygon points="22,909 156,909 164,935 32,935" fill="#fff"/>
    <polygon points="34,918 168,918 176,942 44,942" fill="#3b3b3d"/>
  </svg>
  <div class="t brand-name" style="left:100px;top:58px;font-size:34px">brenlow</div>
  <div class="t brand-sub" style="left:100px;top:89px;font-size:11px">Finance Limited</div>
  <div class="t headline-dark" style="left:98px;top:772px;font-size:28px">BRIDGING</div>
  <div class="t headline-light" style="left:98px;top:809px;font-size:33px">LOAN</div>
  <div class="t headline-light" style="left:98px;top:845px;font-size:33px"><span class="thin">SERVICE</span></div>
  <div class="t tagline" style="left:98px;top:877px;font-size:12px"><span class="rule" style="width:14px"></span>YOU CAN RELY ON<span class="rule" style="width:14px"></span></div>
  <div class="t cta-text" style="left:106px;top:930px;font-size:9.5px">THINK BRENLOW FINANCE</div>
</div>

<!-- 336 x 280 -->
<div class="size-label" style="left:601px;top:1190px">336 x 280 px</div>
<div class="banner rectangle" style="left:318px;top:1240px;width:565px;height:470px">
  <div class="photo" role="img" aria-label="Photo of an open laptop beside printed reports with a pie chart"></div>
  <svg class="shapes" viewBox="0 0 565 470" preserveAspectRatio="none">
    <defs>
      <linearGradient id="og3" x1="0" y1="0" x2="1" y2="1">
        <stop offset="0" stop-color="#f2861c"/><stop offset=".5" stop-color="#f9a036"/><stop offset="1" stop-color="#f2861c"/>
      </linearGradient>
    </defs>
    <polygon points="0,0 290,0 411,276 290,470 0,470" fill="url(#og3)"/>
    <polygon points="411,276 290,470 364,470" fill="#fff"/>
    <polygon points="41,334 278,334 293,390 64,390" fill="#fff"/>
    <polygon points="63,352 296,352 311,393 82,393" fill="#3b3b3d"/>
  </svg>
  <div class="t brand-name" style="left:128px;top:76px;font-size:64px">brenlow</div>
  <div class="t brand-sub" style="left:128px;top:121px;font-size:19px">Finance Limited</div>
  <div class="t left headline-dark" style="left:42px;top:206px;font-size:46px">BRIDGING</div>
  <div class="t left headline-light" style="left:42px;top:256px;font-size:45px">LOAN <span class="thin">SERVICE</span></div>
  <div class="t left tagline" style="left:44px;top:293px;font-size:23px">YOU CAN RELY ON<span class="rule" style="width:62px;margin-left:6px"></span></div>
  <div class="t cta-text" style="left:188px;top:373px;font-size:18px">THINK BRENLOW FINANCE</div>
</div>

<!-- 320 x 100 -->
<div class="size-label" style="left:601px;top:1763px">320 x 100 px</div>
<div class="banner mobile-banner" style="left:331px;top:1806px;width:538px;height:168px">
  <div class="photo" role="img" aria-label="Photo of an open laptop on a desk"></div>
  <svg class="shapes" viewBox="0 0 538 168" preserveAspectRatio="none">
    <defs>
      <linearGradient id="og4" x1="0" y1="0" x2="1" y2="1">
        <stop offset="0" stop-color="#f9a036"/><stop offset="1" stop-color="#f2861c"/>
      </linearGradient>
    </defs>
    <polygon points="289,0 301,0 255,100 247,92" fill="#040303"/>
    <polygon points="301,0 538,0 538,168 300,168 255,100" fill="url(#og4)"/>
    <polygon points="151,130 270,130 288,168 166,168" fill="#fff"/>
    <polygon points="163,137 283,137 300,168 176,168" fill="#3b3b3d"/>
    <circle cx="72" cy="74" r="42" fill="#040303"/>
  </svg>
  <div class="t brand-name" style="left:72px;top:70px;font-size:22px;color:var(--orange)">brenlow</div>
  <div class="t brand-sub" style="left:72px;top:88px;font-size:7px;color:var(--orange)">Finance Limited</div>
  <div class="t headline-dark" style="left:397px;top:56px;font-size:30px">BRIDGING</div>
  <div class="t headline-light" style="left:396px;top:90px;font-size:30px">LOAN <span class="thin">SERVICE</span></div>
  <div class="t tagline" style="left:397px;top:118px;font-size:17px"><span class="rule" style="width:20px"></span>YOU CAN RELY ON<span class="rule" style="width:20px"></span></div>
  <div class="t cta-text" style="left:232px;top:153px;font-size:10.5px">THINK BRENLOW FINANCE</div>
</div>

<!-- 468 x 60 -->
<div class="size-label" style="left:601px;top:2035px">468 x 60 px</div>
<div class="banner leaderboard" style="left:207px;top:2070px;width:786px;height:101px">
  <div class="photo" role="img" aria-label="Photo of an open laptop on a desk with financial reports"></div>
  <svg class="shapes" viewBox="0 0 786 101" preserveAspectRatio="none">
    <defs>
      <linearGradient id="og5" x1="0" y1="0" x2="1" y2="1">
        <stop offset="0" stop-color="#f9a036"/><stop offset="1" stop-color="#f2861c"/>
      </linearGradient>
    </defs>
    <polygon points="0,0 222,0 67,101 0,101" fill="url(#og5)"/>
    <polygon points="222,0 293,0 67,101" fill="#fff"/>
    <polygon points="0,74 0,101 58,101" fill="#040303"/>
    <polygon points="470,0 479,0 470,34 503,101 494,101 461,34" fill="#040303"/>
    <polygon points="479,0 786,0 786,101 503,101 470,34" fill="url(#og5)"/>
    <polygon points="372,65 478,65 491,91 384,91" fill="#fff"/>
    <polygon points="381,71 488,71 501,101 393,101" fill="#3b3b3d"/>
  </svg>
  <div class="t brand-name" style="left:73px;top:38px;font-size:32px">brenlow</div>
  <div class="t brand-sub" style="left:73px;top:60px;font-size:9px">Finance Limited</div>
  <div class="t left headline-dark" style="left:535px;top:27px;font-size:27px">BRIDGING</div>
  <div class="t left headline-light" style="left:535px;top:58px;font-size:27px">LOAN <span class="thin">SERVICE</span></div>
  <div class="t left tagline" style="left:537px;top:83px;font-size:15px">YOU CAN RELY ON<span class="rule" style="width:40px;margin-left:6px"></span></div>
  <div class="t cta-text" style="left:440px;top:86px;font-size:8.5px">THINK BRENLOW FINANCE</div>
</div>

</body>
</html>
```